Nanny Share Ecommerce Website for Finding Childcare and Parents who need Childcare BrightPramHub.net

Our company needs an ecommerce website (BrightPramHub.net) for a US subscription based service strictly for nanny sharing that connects families and caregivers. The website would allow families to connect with one another as well as to search for nannies. The service would be searchable for other families by location (by radius or zip code), children demographic (age range/gender/special needs), days of week or times, after school care, school closure days (holidays), etc. The service would also be searchable for nannies based on gender, provider age range, years experience, language, hourly rate, transportation available, certification (CPR first aid), education etc. The search fields would be searchable and sortable and allow to connect with the provider (after paying subscription fee). The service would be similar to tendlyfolk.net in that it would allow for families and caregivers to post photos as well as a short bio of the themselves. There would also be a feedback/star rating mechanism to rate caregivers who have performed work for families (viewable to public). The service would be free for nannies to post their bios and only a subscription based service for families to connect with other families or with caregivers (able to view bio but need service to connect). There will be a short bio on the benefits of nanny sharing (reduced cost, increased flexibility for parents, reduced illness, increased socialization with other children vs. sole nanny), as well as Q&A section with best practices.

Target Market(s)

Families, Nannies

Industry/Entity Type

Childcare

Logo Text

Bright Pram Hub

Coding

Coded - Design and coding required

Number of Pages Required

5+ page

Requirements
Must have
• Searchable (need to be able to search for families as well as nannies), responsive, functional, easy to use, add value to families and nannies. Needs to be able to collect payment for subscription.
Nice to have
• Optimized for mobile, SEO optimized

```html
<!DOCTYPE html>
<html lang="en">
<head>
<meta charset="utf-8">
<title>Bright Pram Hub</title>
<link rel="stylesheet" href="https://fonts.googleapis.com/css2?family=Open+Sans:wght@400;600;700&family=Raleway:wght@500;600;700&display=swap">
<style>
:root{
  --blue:#1b8fd8;
  --orange:#ef5a23;
  --ink:#222;
  --text:#555;
  --muted:#777;
  --gray-band:#f1f1f1;
  --line:#e3e3e3;
  --footer:#222222;
  --white:#fff;
}
*{box-sizing:border-box;margin:0;padding:0}
html,body{width:1200px;height:4072px;overflow:hidden}
body{font-family:"Open Sans",Arial,sans-serif;color:var(--text);background:var(--white);position:relative}
.section-title{position:absolute;left:0;width:1200px;text-align:center;font-family:"Raleway",Arial,sans-serif;font-weight:600;font-size:26px;color:var(--blue)}
.section-title::after{content:"";display:block;width:50px;height:2px;background:#cfe6f5;margin:14px auto 0}
.btn{display:inline-block;background:var(--orange);color:var(--white);font-size:10px;font-weight:600;text-transform:uppercase;padding:5px 10px;letter-spacing:.3px}

/* header & hero */
.hero{position:absolute;left:0;top:0;width:1200px;height:657px;background:linear-gradient(135deg,#d9cfc0 0%,#eae4da 35%,#c9b8a5 60%,#9fb4c4 100%)}
.logo{position:absolute;left:130px;top:20px;font-family:"Raleway",Arial,sans-serif;font-weight:600;font-size:29px;color:var(--blue)}
.nav{position:absolute;top:20px;left:638px;display:flex;align-items:center}
.nav a{font-size:13px;font-weight:600;color:var(--ink);text-decoration:none;padding:7px 9px;text-transform:uppercase}
.nav a.active{background:var(--blue);color:var(--white)}
.nav svg{margin-left:12px}
.hero-box{position:absolute;left:361px;top:388px;width:486px;height:169px;background:rgba(50,50,50,.55)}
.hero-title{position:absolute;left:0;top:22px;width:486px;text-align:center;font-family:"Raleway",Arial,sans-serif;font-weight:700;font-size:34px;color:var(--white);letter-spacing:.5px}
.hero-actions{position:absolute;left:30px;top:88px;display:flex;gap:20px}
.hero-actions span{display:block;font-size:17px;font-weight:600;color:var(--white);padding:13px 0;text-align:center}
.hero-actions .find{background:var(--orange);width:175px}
.hero-actions .search{background:var(--blue);width:232px}
.dots{position:absolute;top:602px;left:538px;display:flex;gap:12px}
.dots i{width:9px;height:9px;border-radius:50%;background:#555;display:block}
.dots i.on{background:var(--blue)}

/* services */
.service{position:absolute;top:801px;width:223px;height:407px;background:var(--white);box-shadow:0 1px 6px rgba(0,0,0,.12)}
.service .photo{height:252px;position:relative}
.service .photo h3{position:absolute;left:18px;bottom:12px;font-family:"Raleway",Arial,sans-serif;font-weight:600;font-size:17px;color:var(--white)}
.service ul{list-style:none;padding:16px 18px 0 18px}
.service li{font-size:10.5px;color:var(--text);line-height:19px;padding-left:12px;position:relative}
.service li::before{content:"";position:absolute;left:0;top:8px;width:4px;height:4px;border-radius:50%;background:#888}
.service .btn{margin:14px 0 0 18px}

/* welcome */
.welcome{position:absolute;left:0;top:1279px;width:1200px;height:459px;background:linear-gradient(90deg,#ece8e0 0%,#e4ddd0 45%,#d8c9b8 70%,#b9c7a3 100%)}
.welcome-box{position:absolute;left:136px;top:97px;width:426px;height:248px;background:rgba(255,255,255,.85);padding:28px 40px}
.welcome-box h2{font-family:"Raleway",Arial,sans-serif;font-weight:600;font-size:24px;color:var(--ink);margin-bottom:14px}
.welcome-box p{font-size:13px;line-height:21px;color:var(--text);margin-bottom:14px}

/* benefits */
.benefit{position:absolute;top:1890px;width:216px;text-align:center}
.benefit .icon{height:70px;display:flex;justify-content:center;align-items:center}
.benefit h3{font-family:"Raleway",Arial,sans-serif;font-weight:600;font-size:16px;color:var(--ink);line-height:21px;height:60px;display:flex;align-items:center;justify-content:center;margin-top:10px}
.benefit p{font-size:12px;line-height:19px;color:var(--text);margin:10px auto 0;max-width:210px}

/* faq */
.faq{position:absolute;left:0;top:2186px;width:1200px;height:469px;background:var(--gray-band)}
.faq-row{position:absolute;width:442px;height:44px;background:var(--white);font-size:12px;color:var(--text);padding:0 18px;display:flex;align-items:center;justify-content:space-between}

/* blog */
.post{position:absolute;top:2813px;width:291px}
.post .photo{height:206px}
.post h3{font-family:"Raleway",Arial,sans-serif;font-weight:600;font-size:15px;color:var(--ink);line-height:20px;margin-top:22px}
.post p{font-size:12.5px;line-height:19px;color:var(--text);margin-top:8px;margin-bottom:12px}

/* reviews */
.reviews{position:absolute;left:0;top:3250px;width:1200px;height:443px;background:var(--gray-band)}
.review{position:absolute;top:141px;width:430px;height:262px;background:var(--white);padding:30px 30px 0 58px}
.review .q{position:absolute;font-family:Georgia,serif;font-size:56px;color:#ccc;line-height:1}
.review p{font-size:12.5px;line-height:20px;color:var(--text)}
.stars{color:var(--orange);font-size:13px;letter-spacing:1px;margin-top:18px}
.reviewer{display:flex;align-items:center;gap:10px;margin-top:14px}
.reviewer .avatar{width:34px;height:34px;border-radius:50%;background:#b89a82}
.reviewer b{display:block;font-size:10px;font-weight:600;color:var(--ink)}
.reviewer span{font-size:10px;color:var(--muted)}
.arrow{position:absolute;top:255px}

/* footer */
.footer{position:absolute;left:0;top:3693px;width:1200px;height:379px;background:var(--footer);color:#ddd}
.footer .brand{position:absolute;left:130px;top:60px;font-family:"Raleway",Arial,sans-serif;font-weight:600;font-size:29px;color:var(--blue)}
.footer h4{font-size:11px;font-weight:700;color:var(--white);text-transform:uppercase;letter-spacing:.5px}
.follow{position:absolute;left:206px;top:122px;text-align:center}
.social{display:flex;gap:10px;margin-top:14px}
.social i{display:block;width:26px;height:26px;border-radius:50%;background:var(--blue)}
.contact{position:absolute;left:415px;top:64px}
.contact li{list-style:none;display:flex;gap:10px;font-size:10.5px;line-height:15px;margin-top:14px;color:#ccc}
.menu{position:absolute;left:600px;top:64px}
.menu li{list-style:none;font-size:11px;line-height:16px;color:#ccc}
.menu ul{margin-top:14px}
.feedback{position:absolute;left:730px;top:64px;width:340px}
.field{background:var(--white);height:34px;font-size:11px;color:#555;padding:9px 8px}
.feedback .pair{display:flex;gap:10px;margin-top:18px}
.feedback .pair .field{width:165px}
.feedback .message{height:68px;margin-top:10px}
.feedback .btn{margin-top:14px;padding:7px 12px}
.footer .rule{position:absolute;left:130px;top:293px;width:940px;height:1px;background:#3a3a3a}
.copyright{position:absolute;left:0;top:336px;width:1200px;text-align:center;font-size:11px;color:#aaa}
</style>
</head>
<body>

<header class="hero" role="img" aria-label="Photo of a smiling caregiver playing with four young children on a bright playroom floor">
  <div class="logo">Bright Pram Hub</div>
  <nav class="nav">
    <a class="active">Home</a><a>About Us</a><a>Services</a><a>Blog</a><a>Contact Us</a>
    <svg width="14" height="14" viewBox="0 0 14 14"><circle cx="5.5" cy="5.5" r="4.3" fill="none" stroke="#222" stroke-width="1.8"/><line x1="8.7" y1="8.7" x2="13" y2="13" stroke="#222" stroke-width="2"/></svg>
  </nav>
  <div class="hero-box">
    <h1 class="hero-title">CHILD CARE SERVICE</h1>
    <div class="hero-actions"><span class="find">Find Care</span><span class="search">Search for Nannies</span></div>
  </div>
  <div class="dots"><i></i><i></i><i class="on"></i><i></i><i></i></div>
</header>

<h2 class="section-title" style="top:708px">Our Services</h2>

<article class="service" style="left:130px">
  <div class="photo" role="img" aria-label="Photo of a mother and daughter" style="background:linear-gradient(160deg,#c2543f,#e09a80 55%,#7a3b2c)"><h3>Child Care</h3></div>
  <ul><li>Lorem Ipsum is simply</li><li>Contrary to popular belie</li><li>There are many variations</li><li>It is a long establish</li></ul>
  <span class="btn">Read More</span>
</article>
<article class="service" style="left:369px">
  <div class="photo" role="img" aria-label="Photo of a carer helping an elderly man" style="background:linear-gradient(160deg,#d8d0c6,#a89c90 55%,#3f3a36)"><h3>Senior Care</h3></div>
  <ul><li>Lorem Ipsum is simply</li><li>Contrary to popular belie</li><li>There are many variations</li><li>It is a long establish</li></ul>
  <span class="btn">Read More</span>
</article>
<article class="service" style="left:608px">
  <div class="photo" role="img" aria-label="Photo of a small white dog" style="background:linear-gradient(160deg,#7c7c7c,#cfcfcf 50%,#555)"><h3>Pet Care</h3></div>
  <ul><li>Lorem Ipsum is simply</li><li>Contrary to popular belie</li><li>There are many variations</li><li>It is a long establish</li></ul>
  <span class="btn">Read More</span>
</article>
<article class="service" style="left:847px">
  <div class="photo" role="img" aria-label="Photo of a housekeeper cleaning a room" style="background:linear-gradient(160deg,#e6e1d8,#b88f7a 55%,#5d4a3e)"><h3>Housekeeping</h3></div>
  <ul><li>Lorem Ipsum is simply</li><li>Contrary to popular belie</li><li>There are many variations</li><li>It is a long establish</li></ul>
  <span class="btn">Read More</span>
</article>

<section class="welcome" role="img" aria-label="Photo of a young carer embracing a smiling elderly woman in a bright room">
  <div class="welcome-box">
    <h2>Welcome to our site</h2>
    <p>There are many variations of passages of Lorem Ipsum available, but the majority have suffered alteration in some form, by injected humour, or randomised words which don't look even slightly believable. If you are going to use a passage,embarrassing .</p>
    <span class="btn">Read More</span>
  </div>
</section>

<h2 class="section-title" style="top:1782px">Benefits</h2>

<div class="benefit" style="left:120px">
  <div class="icon"><svg width="40" height="64" viewBox="0 0 40 64"><text x="20" y="54" text-anchor="middle" font-family="Arial" font-weight="700" font-size="62" fill="#1b8fd8">$</text></svg></div>
  <h3>Reduced cost</h3>
  <p>There are many variations of passages of Lorem Ipsum available, but the majority have suffered alteration in some form.</p>
</div>
<div class="benefit" style="left:362px">
  <div class="icon"><svg width="62" height="56" viewBox="0 0 62 56"><circle cx="19" cy="12" r="9" fill="#1b8fd8"/><circle cx="43" cy="12" r="9" fill="#1b8fd8"/><path d="M2 50c0-17 8-26 17-26s15 6 12 12l-8 14z" fill="#1b8fd8"/><path d="M60 50c0-17-8-26-17-26s-15 6-12 12l8 14z" fill="#1b8fd8"/><path d="M31 52l-9-9a5 5 0 0 1 9-5 5 5 0 0 1 9 5z" fill="#fff"/></svg></div>
  <h3>Increased<br>flexibility for parents</h3>
  <p>There are many variations of passages of Lorem Ipsum available, but the majority have suffered alteration in some form.</p>
</div>
<div class="benefit" style="left:606px">
  <div class="icon"><svg width="64" height="56" viewBox="0 0 64 56"><path d="M32 54L8 30A14 14 0 0 1 32 10a14 14 0 0 1 24 20z" fill="#1b8fd8"/><polyline points="2,30 20,30 26,20 33,40 39,26 44,30 62,30" fill="none" stroke="#fff" stroke-width="3"/></svg></div>
  <h3>Reduced illness</h3>
  <p>There are many variations of passages of Lorem Ipsum available, but the majority have suffered alteration in some form.</p>
</div>
<div class="benefit" style="left:861px">
  <div class="icon"><svg width="50" height="64" viewBox="0 0 50 64"><rect x="14" y="2" width="22" height="12" rx="2" fill="none" stroke="#1b8fd8" stroke-width="2"/><circle cx="25" cy="26" r="9" fill="none" stroke="#1b8fd8" stroke-width="2.5"/><path d="M6 62c0-14 8-22 19-22s19 8 19 22z" fill="#1b8fd8"/><rect x="22" y="44" width="6" height="14" fill="#fff"/></svg></div>
  <h3>Increased Socialization</h3>
  <p>There are many variations of passages of Lorem Ipsum available, but the majority have suffered alteration in some form.</p>
</div>

<section class="faq">
  <h2 class="section-title" style="top:44px">FAQ</h2>
  <div class="faq-row" style="left:149px;top:135px">Lorem Ipsum is simply dummy text of the printing?<svg width="10" height="6"><polyline points="1,1 5,5 9,1" fill="none" stroke="#777" stroke-width="1.5"/></svg></div>
  <div class="faq-row" style="left:149px;top:192px">There are many variations of passages?<svg width="10" height="6"><polyline points="1,1 5,5 9,1" fill="none" stroke="#777" stroke-width="1.5"/></svg></div>
  <div class="faq-row" style="left:149px;top:249px">Sed ut perspiciatis unde omnis iste natus error?<svg width="10" height="6"><polyline points="1,1 5,5 9,1" fill="none" stroke="#777" stroke-width="1.5"/></svg></div>
  <div class="faq-row" style="left:149px;top:306px">At vero eos et accusamus et iusto od?<svg width="10" height="6"><polyline points="1,1 5,5 9,1" fill="none" stroke="#777" stroke-width="1.5"/></svg></div>
  <div class="faq-row" style="left:149px;top:363px">On the other hand, we denounce with righteou?<svg width="10" height="6"><polyline points="1,1 5,5 9,1" fill="none" stroke="#777" stroke-width="1.5"/></svg></div>
  <div class="faq-row" style="left:609px;top:135px">It is a long established fact that a reader?<svg width="10" height="6"><polyline points="1,1 5,5 9,1" fill="none" stroke="#777" stroke-width="1.5"/></svg></div>
  <div class="faq-row" style="left:609px;top:192px">Many desktop publishing packages and web?<svg width="10" height="6"><polyline points="1,1 5,5 9,1" fill="none" stroke="#777" stroke-width="1.5"/></svg></div>
  <div class="faq-row" style="left:609px;top:249px">But I must explain to you how all this mistaken idea?<svg width="10" height="6"><polyline points="1,1 5,5 9,1" fill="none" stroke="#777" stroke-width="1.5"/></svg></div>
  <div class="faq-row" style="left:609px;top:306px">It is a long established fact that a reader?<svg width="10" height="6"><polyline points="1,1 5,5 9,1" fill="none" stroke="#777" stroke-width="1.5"/></svg></div>
  <div class="faq-row" style="left:609px;top:363px">Bound to ensue; and equal blame belongs to those wh?<svg width="10" height="6"><polyline points="1,1 5,5 9,1" fill="none" stroke="#777" stroke-width="1.5"/></svg></div>
</section>

<h2 class="section-title" style="top:2706px">Latest Blog</h2>

<article class="post" style="left:130px">
  <div class="photo" role="img" aria-label="Photo of a carer holding an elderly person's hands" style="background:linear-gradient(160deg,#e8ecef,#c9cfd6 50%,#8a9aa8)"></div>
  <h3>At vero eos et accusamus et iusto<br>odio dignissimo</h3>
  <p>On the other hand, we denounce with righteous indignation and dislike men who are so beguiled and demoralized by the charms.</p>
  <span class="btn">Read More</span>
</article>
<article class="post" style="left:453px">
  <div class="photo" role="img" aria-label="Photo of children playing with an abacus in a classroom" style="background:linear-gradient(160deg,#c99a5a,#e4c48a 45%,#a1423a)"></div>
  <h3>At vero eos et accusamus et iusto<br>odio dignissimo</h3>
  <p>On the other hand, we denounce with righteous indignation and dislike men who are so beguiled and demoralized by the charms.</p>
  <span class="btn">Read More</span>
</article>
<article class="post" style="left:779px">
  <div class="photo" role="img" aria-label="Photo of a caregiver drawing with a young child" style="background:linear-gradient(160deg,#d9c8b6,#c79680 50%,#8a5f4a)"></div>
  <h3>At vero eos et accusamus et iusto<br>odio dignissimo</h3>
  <p>On the other hand, we denounce with righteous indignation and dislike men who are so beguiled and demoralized by the charms.</p>
  <span class="btn">Read More</span>
</article>

<section class="reviews">
  <h2 class="section-title" style="top:60px">Review</h2>
  <svg class="arrow" style="left:74px" width="14" height="24" viewBox="0 0 14 24"><polyline points="12,2 2,12 12,22" fill="none" stroke="#999" stroke-width="2"/></svg>
  <svg class="arrow" style="left:1114px" width="14" height="24" viewBox="0 0 14 24"><polyline points="2,2 12,12 2,22" fill="none" stroke="#999" stroke-width="2"/></svg>
  <div class="review" style="left:163px">
    <span class="q" style="left:20px;top:14px">&ldquo;</span>
    <p>Lorem Ipsum is simply dummy text of the printing and typesetting industry. Lorem Ipsum has been the industry's standard dummy text ever since the 1500s, when an unknown printer took a galley of type and scrambled</p>
    <span class="q" style="left:276px;top:118px">&rdquo;</span>
    <div class="stars">★★★★★</div>
    <div class="reviewer"><div class="avatar" role="img" aria-label="Reviewer portrait"></div><div><b>Marla Quint</b><span>England</span></div></div>
  </div>
  <div class="review" style="left:619px">
    <span class="q" style="left:20px;top:14px">&ldquo;</span>
    <p>Lorem Ipsum is simply dummy text of the printing and typesetting industry. Lorem Ipsum has been the industry's standard dummy text ever since the 1500s, when an unknown printer took a galley of type and scrambled</p>
    <span class="q" style="left:276px;top:118px">&rdquo;</span>
    <div class="stars">★★★★★</div>
    <div class="reviewer"><div class="avatar" role="img" aria-label="Reviewer portrait"></div><div><b>Marla Quint</b><span>England</span></div></div>
  </div>
</section>

<footer class="footer">
  <div class="brand">Bright Pram Hub</div>
  <div class="follow"><h4>Follow Us</h4><div class="social"><i></i><i></i><i></i></div></div>
  <div class="contact">
    <h4>Contact Us</h4>
    <ul>
      <li><svg width="10" height="14" viewBox="0 0 10 14"><path d="M5 0a5 5 0 0 1 5 5c0 4-5 9-5 9S0 9 0 5a5 5 0 0 1 5-5z" fill="#ddd"/><circle cx="5" cy="5" r="2" fill="#222"/></svg><span>418 Orchard Lane<br>Millbrook, IL 60000</span></li>
      <li><svg width="10" height="12" viewBox="0 0 10 12"><path d="M2 0h2l1 3-1.5 1.5a7 7 0 0 0 3 3L8 6l2 1v2.5A2 2 0 0 1 8 11C3 11 0 6 0 2a2 2 0 0 1 2-2z" fill="#ddd"/></svg><span>555.014.2231</span></li>
      <li><svg width="12" height="10" viewBox="0 0 12 10"><rect width="12" height="10" fill="#ddd"/><polyline points="0,0 6,5 12,0" fill="none" stroke="#222" stroke-width="1.2"/></svg><span>hello@brightpramhub.net</span></li>
    </ul>
  </div>
  <div class="menu">
    <h4>Menu</h4>
    <ul><li>Home</li><li>About Us</li><li>Services</li><li>Blog</li><li>Contact Us</li></ul>
  </div>
  <div class="feedback">
    <h4>Feedback</h4>
    <div class="pair"><div class="field">Name</div><div class="field">E-mail Id</div></div>
    <div class="field message">Message</div>
    <span class="btn">Submit</span>
  </div>
  <div class="rule"></div>
  <div class="copyright">Copyrights @ 2018 All Rights Reserved</div>
</footer>

</body>
</html>
```